BOLD & MINIMALIST DESIGN NEEDED

We want a very bold but minimalistic business card design that is impactful and utilizes both sides of the business card. Our current logo is included for your use.

We want bold fonts and good use of negative space. We don't want the logo to overpower the design.

Target Market(s)

Professionals who are building new commercial buildings.

Industry/Entity Type

Construction

Contact Information for Business Card

Name, Title, email, office phone, cell phone, website

Font styles to use
Serif
Sans Serif

Requirements
Must have
• Bold design!

```html
<!DOCTYPE html>
<html lang="en">
<head>
<meta charset="utf-8">
<title>Ridgeline Design + Build — Business Card</title>
<link rel="stylesheet" href="https://fonts.googleapis.com/css2?family=Montserrat:wght@400;500;800&family=Oswald:wght@600&display=swap">
<style>
  :root {
    --canvas: #f2f2f2;
    --paper: #f4f4f4;
    --ink: #141414;
    --ink-soft: #1f1f1f;
    --lime: #7cc534;
    --text-light: #eaeaea;
    --text-dark: #161616;
  }
  * { box-sizing: border-box; margin: 0; padding: 0; }
  html, body {
    width: 1200px; height: 800px; overflow: hidden;
    background: var(--canvas);
  }
  .sheet {
    width: 1200px; height: 800px;
    display: flex; align-items: center; justify-content: center; gap: 40px;
  }
  .card {
    width: 540px; height: 309px; position: relative; overflow: hidden;
    box-shadow: 0 10px 28px rgba(0,0,0,.14);
  }

  /* Front */
  .card--front { background: var(--paper); }
  .front__brand {
    position: absolute; top: 46px; left: 0; right: 0;
    display: flex; flex-direction: column; align-items: center; gap: 6px;
  }
  .wordmark {
    display: flex; align-items: center; gap: 10px;
    font-family: "Montserrat", sans-serif; font-weight: 800;
    letter-spacing: .02em; color: var(--text-dark);
    font-size: 30px; line-height: 1;
  }
  .wordmark__square { width: 16px; height: 16px; background: var(--lime); }
  .wordmark__sub {
    font-family: "Montserrat", sans-serif; font-weight: 800;
    font-size: 11px; letter-spacing: .42em; color: var(--text-dark);
  }
  .front__band {
    position: absolute; left: 0; right: 0; bottom: 0; height: 150px;
    background: var(--ink); border-top: 3px solid var(--lime);
  }
  .contact {
    position: absolute; left: 26px; top: 26px;
    list-style: none; font-family: "Montserrat", sans-serif;
    font-size: 12.5px; color: var(--text-light); line-height: 1.55;
  }
  .contact li { display: flex; align-items: center; gap: 8px; }
  .contact svg { width: 12px; height: 12px; flex: none; }
  .contact .accent { color: var(--lime); }
  .person {
    position: absolute; right: 26px; bottom: 26px; text-align: right;
  }
  .person__name {
    font-family: "Oswald", sans-serif; font-weight: 600;
    font-size: 30px; color: var(--lime); line-height: 1; letter-spacing: .01em;
  }
  .person__title {
    font-family: "Montserrat", sans-serif; font-weight: 400;
    font-size: 12px; letter-spacing: .08em; color: var(--text-light); margin-top: 4px;
  }

  /* Back */
  .card--back {
    background: var(--ink-soft);
    display: flex; flex-direction: column; align-items: center; justify-content: center; gap: 8px;
  }
  .card--back .wordmark { color: #f2f2f2; font-size: 40px; }
  .card--back .wordmark__sub { color: #e0e0e0; font-size: 13px; }
  .card--back .rule { width: 300px; height: 2px; background: #e0e0e0; }
</style>
</head>
<body>
<main class="sheet">

  <section class="card card--front" aria-label="Business card front">
    <div class="front__brand">
      <div class="wordmark"><span class="wordmark__square"></span>RIDGELINE</div>
      <div class="wordmark__sub">DESIGN + BUILD</div>
    </div>
    <div class="front__band">
      <ul class="contact">
        <li>
          <svg viewBox="0 0 24 24" fill="var(--lime)"><path d="M6.6 10.8a15 15 0 006.6 6.6l2.2-2.2a1 1 0 011-.25 11.4 11.4 0 003.6.57 1 1 0 011 1V20a1 1 0 01-1 1A17 17 0 013 4a1 1 0 011-1h3.5a1 1 0 011 1c0 1.25.2 2.45.57 3.6a1 1 0 01-.25 1z"/></svg>
          (555) 214-7730
        </li>
        <li>
          <svg viewBox="0 0 24 24" fill="var(--lime)"><rect x="6" y="2" width="12" height="20" rx="2"/><rect x="8" y="4" width="8" height="13" fill="var(--ink)"/></svg>
          (555) 214-7731
        </li>
        <li>
          <svg viewBox="0 0 24 24" fill="none" stroke="var(--lime)" stroke-width="2"><rect x="3" y="5" width="18" height="14"/><path d="M3 6l9 7 9-7"/></svg>
          ridgelinebuild@mail.com
        </li>
        <li>
          <svg viewBox="0 0 24 24" fill="none" stroke="var(--lime)" stroke-width="2"><circle cx="12" cy="12" r="9"/><path d="M3 12h18M12 3c3 3 3 15 0 18M12 3c-3 3-3 15 0 18"/></svg>
          <span>www.<span class="accent">ridgelinebuild</span>.com</span>
        </li>
      </ul>
      <div class="person">
        <div class="person__name">MARK DELANEY</div>
        <div class="person__title">OWNER</div>
      </div>
    </div>
  </section>

  <section class="card card--back" aria-label="Business card back">
    <div class="wordmark">RIDGELINE</div>
    <div class="rule"></div>
    <div class="wordmark__sub">DESIGN + BUILD</div>
  </section>

</main>
</body>
</html>
```